Book Cover for Lanterns Along the Quiet Threshold

I need a book cover for a 6 x 9 paperback titled Lanterns Along the Quiet Threshold Gathered from Research and Voices Dwelling in the Realm beyond Our Present Days. It has to do with consciousness, the mind, incarnation onto Earth, leaving Earth, and the life in the life after this life. I have an idea I'm providing with this description, but I am open to anything that would be striking and stimulating, whether with a book or not. I am the author, T. Morgan Wexley. I've added another background idea to see if anyone can do something with it and I've increased the budget.

```html
<!DOCTYPE html>
<html lang="en">
<head>
<meta charset="utf-8">
<title>Lanterns Along the Quiet Threshold — Cover</title>
<link href="https://fonts.googleapis.com/css2?family=Tinos:ital,wght@0,400;0,700;1,400&display=swap" rel="stylesheet">
<style>
  :root {
    --backdrop: #7d7e80;
    --space-deep: #1c1a3f;
    --space-violet: #4a2f6e;
    --nebula-rose: #9a5d86;
    --nebula-amber: #c08a6a;
    --horizon-glow: #ffd58a;
    --earth-cloud: #dfe6f1;
    --earth-blue: #5d6f9c;
    --title-white: #f4f2f6;
    --page-cream: #f1e2bb;
    --page-edge: #b88a4a;
    --ink-dark: #1d1712;
    --author-ink: #0d0b10;
  }
  * { margin: 0; padding: 0; box-sizing: border-box; }
  html, body {
    width: 1200px; height: 1200px; overflow: hidden;
    background: var(--backdrop);
  }
  .canvas {
    width: 1200px; height: 1200px;
    display: flex; align-items: center; justify-content: center;
  }
  .cover {
    position: relative;
    width: 720px; height: 1080px;
    overflow: hidden;
    font-family: "Tinos", "Times New Roman", serif;
    box-shadow: 0 10px 30px rgba(0,0,0,.35);
  }
  .cover__starfield {
    position: absolute; inset: 0;
    background:
      radial-gradient(ellipse 45% 30% at 30% 62%, rgba(192,138,106,.55), transparent 70%),
      radial-gradient(ellipse 30% 45% at 60% 25%, rgba(154,93,134,.55), transparent 70%),
      linear-gradient(180deg, var(--space-violet) 0%, var(--space-deep) 55%, #2a2450 78%);
  }
  .cover__traveler {
    position: absolute; left: 295px; top: 225px;
    width: 150px; height: 80px; border-radius: 40px;
    background: radial-gradient(ellipse at center, rgba(225,232,240,.55), rgba(225,232,240,0) 70%);
  }
  .cover__earth {
    position: absolute; left: 0; right: 0; bottom: 0; height: 230px;
    background:
      radial-gradient(ellipse 40% 30% at 50% 8%, var(--horizon-glow), transparent 75%),
      linear-gradient(180deg, rgba(255,213,138,.0) 0%, var(--earth-cloud) 18%, #c9d1e4 45%, var(--earth-blue) 70%, #e8c98f 100%);
  }
  .cover__open-book {
    position: absolute; left: 60px; top: 615px;
    width: 600px; height: 170px;
    border-radius: 10px 10px 4px 4px;
    background:
      radial-gradient(ellipse 55% 80% at 50% 0%, rgba(255,255,255,.7), transparent 70%),
      linear-gradient(180deg, var(--page-cream) 0%, #e2c992 75%, var(--page-edge) 100%);
  }
  .cover__glow {
    position: absolute; left: 150px; top: 520px;
    width: 420px; height: 160px;
    background: radial-gradient(ellipse at center, rgba(255,255,255,.55), transparent 70%);
  }
  .title {
    position: absolute; left: 0; right: 0; top: 408px;
    text-align: center; color: var(--title-white);
    text-transform: uppercase; line-height: .9;
    text-shadow: 0 2px 6px rgba(20,10,40,.6);
  }
  .title__line { display: block; font-size: 58px; letter-spacing: 1px; }
  .title__line--large { font-size: 86px; }
  .title__keyword {
    position: absolute; left: 0; right: 0; top: 652px;
    text-align: center; color: var(--ink-dark);
    font-size: 66px; font-style: italic; text-transform: uppercase;
    letter-spacing: 1px;
  }
  .subtitle {
    position: absolute; left: 0; right: 0; top: 800px;
    text-align: center; color: var(--title-white);
    font-size: 24px; line-height: 1.25;
    text-shadow: 0 1px 4px rgba(0,0,0,.6);
  }
  .author {
    position: absolute; left: 0; right: 0; top: 940px;
    text-align: center; color: var(--author-ink);
    font-size: 46px; letter-spacing: .5px;
  }
</style>
</head>
<body>
<main class="canvas">
  <section class="cover">
    <div class="cover__starfield" role="img" aria-label="Starry violet night sky with a glowing nebula"></div>
    <div class="cover__traveler" role="img" aria-label="Figure in white floating through space"></div>
    <div class="cover__earth" role="img" aria-label="Earth's cloudy horizon seen from orbit with a sunrise glow"></div>
    <div class="cover__glow" aria-hidden="true"></div>
    <div class="cover__open-book" role="img" aria-label="Open glowing book with cream pages"></div>

    <h1 class="title">
      <span class="title__line">Lanterns</span>
      <span class="title__line">Along the</span>
      <span class="title__line title__line--large">Quiet</span>
    </h1>
    <div class="title__keyword">Threshold</div>

    <p class="subtitle">Gathered from Research and Voices Dwelling<br>in the Realm beyond Our Present Days</p>

    <p class="author">T. Morgan Wexley</p>
  </section>
</main>
</body>
</html>
```